Create a memorable Web Design for real estate branding

we are a Minnepolis brokerage and boutique housing specialist with over 27 years of experience in the Global furnished housing industry, servicing the Greater Los Angeles area. Specializing in “warm environments” we offer a customized approach to satisfying our guests and client’s needs by offering a wide array of options in highly desirable areas. Additionally, Lantern Dwelling Partners offers assistance and expertise to home buyers, sellers and investors.

Industry/Entity Type

Real Estate

Number of Pages Required

1 page

Font styles to use
Serif
Sans Serif
Decorative

```html
<!DOCTYPE html>
<html lang="en">
<head>
<meta charset="utf-8">
<title>Lantern Dwelling Real Estate</title>
<link href="https://fonts.googleapis.com/css2?family=Open+Sans:ital,wght@0,300;0,400;0,600;0,700;1,400&display=swap" rel="stylesheet">
<style>
:root{
  --green:#7dc12a;
  --teal:#1aa58a;
  --ink:#333;
  --text:#555;
  --nav:#3b3b3b;
  --footer:#2f2f2f;
  --footer-base:#242424;
  --line:#dcdcdc;
}
*{margin:0;padding:0;box-sizing:border-box}
html,body{width:763px;height:1200px;overflow:hidden;background:#fff}
body{position:relative;font-family:"Open Sans",Arial,sans-serif;color:var(--text)}
.abs{position:absolute}
.topline{left:0;top:0;width:763px;height:3px;background:var(--teal)}
.brand{left:63px;top:14px;color:var(--green);font-weight:700;line-height:1}
.brand .name{font-size:21px;letter-spacing:.3px}
.brand .sub{font-size:12px;letter-spacing:2.5px;margin-top:6px;padding-left:72px;text-transform:uppercase}
.contact-pill{display:flex;align-items:center;gap:8px;top:23px}
.contact-pill .ico{width:26px;height:26px;border-radius:50%;background:var(--green);display:flex;align-items:center;justify-content:center}
.contact-pill .lbl{font-size:8px;color:var(--ink);line-height:1.3}
.contact-pill .val{font-size:9px;color:var(--green);font-weight:600}
.nav{left:0;top:71px;width:763px;height:35px;background:var(--nav)}
.nav a{position:absolute;top:0;height:35px;line-height:35px;font-size:8px;color:#ddd;text-decoration:none;text-align:center}
.nav a.active{background:var(--green);color:#fff}
.nav .sep{position:absolute;top:0;width:1px;height:35px;background:#4a4a4a}
.search{left:578px;top:80px;width:123px;height:18px;border:1px solid #555;font-size:7px;color:#888;padding:4px 7px}
.hero{left:0;top:106px;width:763px;height:289px;background:linear-gradient(180deg,#6fa7dc 0%,#a8c6dc 25%,#5f6f52 45%,#6b5a48 65%,#5a7a2e 85%,#6fa42c 100%)}
.hero h1{font-size:21px;font-weight:300;color:#fff;white-space:nowrap}
.hero h1 b{font-weight:600}
.btn{display:flex;align-items:center;justify-content:center;color:#fff;font-weight:600;background:var(--green);border-radius:2px;text-decoration:none}
.btn.teal{background:var(--teal)}
h2.section{font-size:17px;font-weight:700;color:var(--ink)}
h3.small{font-size:12px;font-weight:700;color:var(--ink)}
.intro{left:63px;top:451px;font-size:7.5px;color:var(--text)}
.card{width:145px}
.card .photo{height:107px}
.card .title{margin-top:14px;font-size:9px;font-weight:600;color:var(--green)}
.card .addr{margin-top:8px;font-size:7.5px;color:var(--ink);line-height:14px;padding-left:10px;position:relative}
.card .addr svg{position:absolute;left:0;top:2px}
.card .btn{margin-top:7px;width:66px;height:22px;font-size:8px;font-weight:400}
.callout{left:63px;top:710px;width:638px;height:60px;border:1px solid var(--line);border-left:4px solid var(--green)}
.callout p{position:absolute;left:15px;top:13px;width:500px;font-size:9.5px;line-height:18px;color:var(--text)}
.arrows{display:flex;gap:3px}
.arrows span{width:9px;height:9px;border-radius:50%;background:#ccc}
.datebox{left:63px;top:830px;width:38px;height:45px;background:#444;color:#fff;text-align:center}
.datebox .d{font-size:11px;margin-top:4px}
.datebox .m{font-size:6px;line-height:9px}
.news-title{left:115px;top:833px;width:130px;font-size:8.5px;font-weight:600;color:var(--green);line-height:13px}
.news-by{left:116px;top:863px;font-size:5.5px;color:var(--ink)}
.news-body{left:63px;top:884px;width:200px;font-size:7px;line-height:13.6px;color:var(--ink)}
.listing{width:126px}
.listing .photo{height:80px}
.listing .title{margin-top:8px;font-size:8.5px;font-weight:600;color:var(--green);line-height:13px}
.listing .link{margin-top:4px;font-size:5.5px;color:var(--ink);display:flex;align-items:center;gap:3px}
.footer{left:0;top:994px;width:763px;height:175px;background:var(--footer)}
.footer h4{position:absolute;top:25px;font-size:7.5px;font-weight:700;color:#fff;letter-spacing:.3px}
.footer ul{list-style:none;position:absolute;top:44px;font-size:7px;color:#999;line-height:14.2px}
.quote{left:80px;top:53px;width:160px;font-size:6.5px;font-style:italic;color:#888;line-height:13px}
.social li{display:flex;align-items:center;gap:4px;height:25.5px}
.social .dot{width:17px;height:17px;border-radius:50%;background:#555}
.footer-base{left:0;top:1169px;width:763px;height:31px;background:var(--footer-base);font-size:7px;color:#999;text-align:center;line-height:31px}
</style>
</head>
<body>
<div class="abs topline"></div>

<div class="abs brand"><div class="name">Lantern Dwelling</div><div class="sub">Real Estate</div></div>

<div class="abs contact-pill" style="left:438px">
  <div class="ico"><svg width="11" height="11" viewBox="0 0 24 24"><path fill="#fff" d="M6.6 10.8a15.1 15.1 0 0 0 6.6 6.6l2.2-2.2c.3-.3.7-.4 1-.2 1.1.4 2.3.6 3.6.6.6 0 1 .4 1 1V20c0 .6-.4 1-1 1A17 17 0 0 1 3 4c0-.6.4-1 1-1h3.5c.6 0 1 .4 1 1 0 1.3.2 2.5.6 3.6.1.3 0 .7-.2 1z"/></svg></div>
  <div><div class="lbl">Call Us :</div><div class="val">( 555 ) 014 2290</div></div>
</div>
<div class="abs contact-pill" style="left:576px">
  <div class="ico"><svg width="11" height="9" viewBox="0 0 22 16"><rect x="1" y="1" width="20" height="14" rx="1" fill="#fff"/><path d="M1 1l10 8 10-8" stroke="#7dc12a" stroke-width="2" fill="none"/></svg></div>
  <div><div class="lbl">Email Us :</div><div class="val">info@lanterndwelling.com</div></div>
</div>

<nav class="abs nav">
  <a class="active" href="#" style="left:64px;width:64px">Home</a>
  <a href="#" style="left:128px;width:70px">About us</a><span class="sep" style="left:198px"></span>
  <a href="#" style="left:198px;width:70px">Services</a><span class="sep" style="left:268px"></span>
  <a href="#" style="left:268px;width:70px">Features</a><span class="sep" style="left:338px"></span>
  <a href="#" style="left:338px;width:60px">News</a><span class="sep" style="left:398px"></span>
  <a href="#" style="left:398px;width:82px">Testimonials</a><span class="sep" style="left:480px"></span>
  <a href="#" style="left:480px;width:82px">Contact Us</a>
</nav>
<div class="abs search">Search :
  <svg class="abs" style="right:6px;top:5px" width="7" height="7" viewBox="0 0 10 10"><circle cx="4" cy="4" r="3" stroke="#888" fill="none" stroke-width="1.3"/><path d="M6.3 6.3 9 9" stroke="#888" stroke-width="1.3"/></svg>
</div>

<section class="abs hero" role="img" aria-label="Photo of a large two-storey family house with a stone porch, lawn and surrounding trees">
  <h1 class="abs" style="left:63px;top:241px">Specializing in <b>“warm environments”</b></h1>
  <a class="abs btn" style="left:434px;top:240px;width:91px;height:31px;font-size:9px">Contact here!</a>
</section>

<h2 class="abs section" style="left:63px;top:422px">Recent Properties</h2>
<p class="abs intro">Simply dummy text of the printing and typesetting industry. Lorem Ipsum has been the industry's standard dummy text ever since the 1500s...</p>
<a class="abs btn" style="left:590px;top:434px;width:111px;height:28px;font-size:8px">View More properties</a>

<div class="abs card" style="left:63px;top:483px">
  <div class="photo" role="img" aria-label="Modern white villa with a pool at dusk" style="background:linear-gradient(180deg,#3a4f8a,#c9a27a 60%,#3a6f9a)"></div>
  <div class="title">Lorem Ipsum is simply dummy</div>
  <div class="addr"><svg width="6" height="9" viewBox="0 0 10 14"><path fill="#7dc12a" d="M5 0a5 5 0 0 1 5 5c0 4-5 9-5 9S0 9 0 5a5 5 0 0 1 5-5zm0 3a2 2 0 1 0 0 4 2 2 0 0 0 0-4z"/></svg>120 Street name, City name,<br>Country name : 695663</div>
  <a class="btn teal">View details</a>
</div>
<div class="abs card" style="left:227px;top:483px">
  <div class="photo" role="img" aria-label="Grey suburban house with a green lawn" style="background:linear-gradient(180deg,#7fb3e0,#7d8a86 50%,#5a9a2a)"></div>
  <div class="title">Lorem Ipsum is simply dummy</div>
  <div class="addr"><svg width="6" height="9" viewBox="0 0 10 14"><path fill="#7dc12a" d="M5 0a5 5 0 0 1 5 5c0 4-5 9-5 9S0 9 0 5a5 5 0 0 1 5-5zm0 3a2 2 0 1 0 0 4 2 2 0 0 0 0-4z"/></svg>120 Street name, City name,<br>Country name : 695663</div>
  <a class="btn teal">View details</a>
</div>
<div class="abs card" style="left:392px;top:483px">
  <div class="photo" role="img" aria-label="White modern house with a swimming pool" style="background:linear-gradient(180deg,#6b9fd6,#e6e6e2 45%,#4aa8c9)"></div>
  <div class="title">Lorem Ipsum is simply dummy</div>
  <div class="addr"><svg width="6" height="9" viewBox="0 0 10 14"><path fill="#7dc12a" d="M5 0a5 5 0 0 1 5 5c0 4-5 9-5 9S0 9 0 5a5 5 0 0 1 5-5zm0 3a2 2 0 1 0 0 4 2 2 0 0 0 0-4z"/></svg>120 Street name, City name,<br>Country name : 695663</div>
  <a class="btn teal">View details</a>
</div>
<div class="abs card" style="left:556px;top:483px">
  <div class="photo" role="img" aria-label="Grey gabled house with autumn trees" style="background:linear-gradient(180deg,#8fb8e3,#9a9b98 50%,#6a8a3a)"></div>
  <div class="title">Lorem Ipsum is simply dummy</div>
  <div class="addr"><svg width="6" height="9" viewBox="0 0 10 14"><path fill="#7dc12a" d="M5 0a5 5 0 0 1 5 5c0 4-5 9-5 9S0 9 0 5a5 5 0 0 1 5-5zm0 3a2 2 0 1 0 0 4 2 2 0 0 0 0-4z"/></svg>120 Street name, City name,<br>Country name : 695663</div>
  <a class="btn teal">View details</a>
</div>

<div class="abs callout">
  <p>Lorem Ipsum is simply dummy text of the printing and typesetting industry. Lorem Ipsum has been the industry's standard dummy text ever since the 1500s, when an unknown printer took a galley...</p>
  <a class="abs btn" style="left:519px;top:14px;width:100px;height:29px;font-size:9.5px">Contact Here!</a>
</div>

<h3 class="abs small" style="left:63px;top:796px">Company News</h3>
<div class="abs arrows" style="left:229px;top:802px"><span></span><span></span></div>
<div class="abs datebox"><div class="d">28</div><div class="m">January<br>2016</div></div>
<div class="abs news-title">Lorem Ipsum is simply dummy text of the printing</div>
<div class="abs news-by">By Organisation / 3 Comments</div>
<p class="abs news-body">Lorem Ipsum is simply dummy text of the printing and typesetting industry. Lorem Ipsum has been the industry's standard dummy text ever since the 1500s, when an unknown printer took a galley of type and scrambled it to make a type specimen book.</p>

<h3 class="abs small" style="left:292px;top:796px">Top Listed properties</h3>
<div class="abs arrows" style="left:677px;top:805px"><span></span><span></span></div>
<div class="abs listing" style="left:292px;top:830px">
  <div class="photo" role="img" aria-label="Blue-grey house with a garage and driveway" style="background:linear-gradient(180deg,#5f93d3,#8d98a5 55%,#6b8a3a)"></div>
  <div class="title">Lorem Ipsum is simply dummy text of the printing</div>
  <div class="link">Click here for view the project details <svg width="6" height="6" viewBox="0 0 10 10"><circle cx="5" cy="5" r="5" fill="#333"/><path d="M4 3l2 2-2 2" stroke="#fff" fill="none"/></svg></div>
</div>
<div class="abs listing" style="left:434px;top:830px">
  <div class="photo" role="img" aria-label="Terrace lounge with white sofas overlooking a lake" style="background:linear-gradient(180deg,#9ab4c8,#5c6f78 45%,#d8d6d0 70%,#3a3a38)"></div>
  <div class="title">Lorem Ipsum is simply dummy text of the printing</div>
  <div class="link">Click here for view the project details <svg width="6" height="6" viewBox="0 0 10 10"><circle cx="5" cy="5" r="5" fill="#333"/><path d="M4 3l2 2-2 2" stroke="#fff" fill="none"/></svg></div>
</div>
<div class="abs listing" style="left:575px;top:830px">
  <div class="photo" role="img" aria-label="Modern dark house lit warmly at night" style="background:linear-gradient(180deg,#1c2a4a,#3a3530 45%,#d0a060 65%,#2a3a1e)"></div>
  <div class="title">Lorem Ipsum is simply dummy text of the printing</div>
  <div class="link">Click here for view the project details <svg width="6" height="6" viewBox="0 0 10 10"><circle cx="5" cy="5" r="5" fill="#333"/><path d="M4 3l2 2-2 2" stroke="#fff" fill="none"/></svg></div>
</div>

<footer class="abs footer">
  <h4 style="left:66px">TESTIMONIALS</h4>
  <div class="abs" style="left:233px;top:24px;font-size:8px;color:#888">‹ ›</div>
  <div class="abs" style="left:64px;top:44px;font-size:16px;color:#666;font-family:Georgia,serif">“</div>
  <p class="abs quote">Simply dummy text of the printing and typesetting industry. Lorem Ipsum has been the industry's standard dummy text ever since the 1500s, when an unknown printer took a galley of type and scrambled it to make a type specimen book...</p>
  <div class="abs" style="left:238px;top:112px;font-size:16px;color:#666;font-family:Georgia,serif">”</div>
  <div class="abs" role="img" aria-label="Client portrait" style="left:72px;top:126px;width:28px;height:28px;border-radius:50%;background:linear-gradient(180deg,#9aa3ad,#5a6470)"></div>
  <div class="abs" style="left:106px;top:131px;font-size:7px;font-weight:700;color:#ddd">MILES HARWIN</div>
  <div class="abs" style="left:106px;top:143px;font-size:7px;color:#777">Marketing Executive</div>

  <h4 style="left:314px">WELCOME</h4>
  <ul style="left:314px"><li>Home</li><li>About us</li><li>Services</li><li>Features</li><li>News</li><li>Testimonials</li><li>Contact Us</li></ul>

  <h4 style="left:437px">CONTACT US</h4>
  <ul style="left:437px;line-height:16px">
    <li>120 Street name, City name</li>
    <li>Country name : 6959656</li>
    <li style="margin-top:2px"><span style="color:var(--green)">&#9742;</span>&nbsp; ( 555 ) 014 2290</li>
    <li><span style="color:var(--green)">&#9993;</span>&nbsp; info@lanterndwelling.com</li>
  </ul>

  <h4 style="left:593px">FOLLOW US</h4>
  <ul class="social" style="left:593px;top:43px">
    <li><span class="dot"></span>: Porchline</li>
    <li><span class="dot"></span>: Nestcast</li>
    <li><span class="dot"></span>: Brickpost</li>
    <li><span class="dot"></span>: Keystream</li>
  </ul>
</footer>
<div class="abs footer-base">© 2016. Lantern Dwelling. All rights reserved.</div>
</body>
</html>
```